Redesign of LumoWordfind.com in Bootstrap 4

Current design of LumoWordfind.com is not responsive. We need to change it to latest version of Bootstrap 4 keeping essential elements in place.

Apart from home page, we need designs for http://www.lumowordfind.com/meaning/cat also.

Coding

Number of Pages Required

2 page

Colors
34a7d8

Requirements
Must have
• Bootstrap 4

```html
<!DOCTYPE html>
<html lang="en">
<head>
<meta charset="utf-8">
<title>Lumo Wordfind – Home</title>
<link href="https://fonts.googleapis.com/css2?family=Mulish:wght@400;600;700&family=Open+Sans:wght@400;600;700&display=swap" rel="stylesheet">
<style>
:root{
  --brand:#34a7d8;
  --brand-dark:#1f7fae;
  --ink:#222;
  --text:#555;
  --muted:#777;
  --dark:#141414;
  --footer:#1b1e20;
  --orange:#c75a10;
  --grey-band:#e6e6e6;
  --line:#e3e3e3;
  --hero:#c7ced9;
}
*{box-sizing:border-box;margin:0;padding:0}
html,body{width:698px;height:1200px;overflow:hidden}
body{position:relative;background:#fff;font-family:"Open Sans",Arial,sans-serif;color:var(--text);font-size:7px}
.abs{position:absolute}
h1,h2,h3{font-family:"Mulish","Open Sans",sans-serif;font-weight:600;color:var(--ink)}
ul{list-style:none}

/* header */
.brand{left:65px;top:14px;display:flex;align-items:center;gap:5px}
.brand-mark{width:12px;height:12px;border-radius:50%;background:var(--brand)}
.brand-name{font-family:"Mulish",sans-serif;font-weight:700;font-size:15px;color:var(--brand-dark)}
.btn{display:inline-flex;align-items:center;justify-content:center;border-radius:16px;color:#fff;font-size:7px;font-weight:600;gap:3px}
.btn-login{left:450px;top:16px;width:83px;height:30px;background:#222}
.btn-join-top{left:540px;top:16px;width:92px;height:30px;background:linear-gradient(#3fb1e0,#2a8fbe)}
.nav{left:65px;top:58px;width:568px;height:31px;background:var(--dark);display:flex;align-items:center;justify-content:space-around;font-size:7px;font-weight:600;color:#fff}
.nav a{color:#fff;text-decoration:none;position:relative;height:31px;line-height:31px;padding:0 13px}
.nav a.active{color:var(--brand)}
.nav a.active::after{content:"";position:absolute;left:0;right:0;bottom:0;height:3px;background:var(--brand)}
.header-rule{left:0;top:89px;width:698px;height:1px;background:#ddd}

/* hero */
.hero{left:0;top:90px;width:698px;height:271px;background:linear-gradient(90deg,#d9dee6,var(--hero))}
.hero-photo{left:20px;top:0;width:230px;height:271px;background:radial-gradient(ellipse at 45% 55%,#3a4a66 0,#5a6a86 35%,#c7ced9 75%)}
.hero-title{left:261px;top:184px;font-size:17px;letter-spacing:.5px;color:#222}
.search{left:261px;top:220px;width:374px;height:41px;background:#4a4a4a;display:flex;align-items:center;padding:0 10px;gap:6px}
.search-input{flex:1;height:27px;border-radius:14px;background:#fff;display:flex;align-items:center;padding-left:12px;color:#888;font-size:6.5px}
.search-btn{width:82px;height:27px;border-radius:14px;background:linear-gradient(#3fb1e0,#2a8fbe);color:#fff;font-size:9px;font-weight:600;display:flex;align-items:center;justify-content:center}
.search-hint{left:262px;top:268px;font-size:6px;color:#666}
.dots{left:331px;top:337px;display:flex;gap:3px}
.dots span{width:5px;height:5px;border-radius:50%;background:#777}
.dots span.on{background:var(--brand)}

/* sidebar */
.card{left:65px;width:131px;border:1px solid var(--line);background:#fff}
.card-head{height:37px;background:linear-gradient(#2a2a2a,#111);color:#fff;font-family:"Mulish",sans-serif;font-weight:600;font-size:10px;display:flex;align-items:center;justify-content:center;letter-spacing:.3px}
.word-tile{margin:10px auto 14px;width:60px;height:58px;border:1px solid #ddd;box-shadow:0 0 5px rgba(0,0,0,.2);display:flex;align-items:center;justify-content:center;font-family:"Mulish",sans-serif;font-weight:700;font-size:11px;color:#333}
.card p{padding:0 11px 14px;font-size:6.2px;line-height:15px;text-align:justify;text-align-last:center;color:#666}
.card-word{top:379px;height:190px}
.card-tidbit{top:585px;height:234px}

/* main column */
.main{left:210px;width:424px}
.main h2{font-size:14.5px;font-weight:600}
.features{top:389px}
.feature-list{margin-top:10px;display:grid;grid-template-columns:200px 200px;row-gap:7px;font-size:6.2px;color:#666}
.feature-list li{display:flex;align-items:center;gap:4px;height:13px}
.bullet{width:6px;height:6px;border-radius:50%;border:1.5px solid var(--brand);background:#fff;box-shadow:inset 0 0 0 1px var(--brand)}
.btn-cta{margin-top:14px;width:120px;height:34px;border-radius:17px;background:linear-gradient(#e07a25,#b24e0c);color:#fff;font-size:9px;font-weight:700;font-family:"Open Sans",sans-serif;gap:4px}
.divider{height:1px;background:var(--line)}
.crossword{top:551px}
.kicker{margin-top:8px;color:#d4650f;font-size:8px}
.body-text{margin-top:4px;font-size:6.3px;line-height:15px;color:#666;width:300px}
.btn-blue{margin-top:13px;width:92px;height:33px;border-radius:17px;background:linear-gradient(#3fb1e0,#2a8fbe);color:#fff;font-size:9px;font-weight:600}
.crossword-art{left:530px;top:568px;width:104px;height:102px;border-radius:10px;background:linear-gradient(135deg,#555,#2a2a2a)}
.addon{top:714px}
.addon-shot{left:524px;top:730px;width:104px;height:62px;border:1px solid #aac;background:linear-gradient(#f2f6fb,#dbe6f1)}

/* browse */
.browse{left:0;top:837px;width:698px;height:83px;background:var(--grey-band)}
.browse h2{position:absolute;left:64px;top:15px;font-size:15px}
.letters{position:absolute;left:65px;top:45px;display:flex;gap:6.4px}
.letters span{width:16px;height:14px;border-radius:3px;background:linear-gradient(#5a5a5a,#2e2e2e);color:#fff;font-size:6px;font-weight:600;display:flex;align-items:center;justify-content:center}

/* mobile band */
.mobile{left:0;top:920px;width:698px;height:128px;background:var(--brand)}
.mobile h2{position:absolute;left:64px;top:22px;color:#fff;font-size:15px}
.mobile p{position:absolute;left:65px;top:46px;width:480px;color:#fff;font-size:6.2px;line-height:15px}
.phone-art{position:absolute;left:563px;top:20px;width:38px;height:76px;border-radius:6px;background:linear-gradient(135deg,#444,#111)}

/* footer */
.footer{left:0;top:1048px;width:698px;height:152px;background:var(--footer);color:#bbb}
.foot-col{position:absolute;top:22px;width:130px}
.foot-col h3{color:#fff;font-size:8.5px;font-weight:700;padding-bottom:12px;border-bottom:1px solid #2c3033;width:130px}
.foot-col ul{margin-top:8px}
.foot-col li{font-size:6.2px;line-height:18px;display:flex;align-items:center;gap:4px}
.foot-col li::before{content:"";border-left:3px solid var(--brand);border-top:2.5px solid transparent;border-bottom:2.5px solid transparent}
.copyright{position:absolute;left:65px;top:127px;font-size:6px;color:#bbb}
.social{position:absolute;left:574px;top:124px;display:flex;gap:3px}
.social span{width:12px;height:12px;border-radius:2px}
</style>
</head>
<body>

<header>
  <div class="abs brand"><span class="brand-mark"></span><span class="brand-name">Lumo Wordfind</span></div>
  <a class="abs btn btn-login">
    <svg width="6" height="7" viewBox="0 0 6 7"><rect x="0.5" y="3" width="5" height="4" fill="#fff"/><path d="M1.5 3V2a1.5 1.5 0 0 1 3 0v1" stroke="#fff" fill="none"/></svg>LOGIN</a>
  <a class="abs btn btn-join-top">
    <svg width="6" height="7" viewBox="0 0 6 7"><circle cx="3" cy="2" r="1.7" fill="#fff"/><path d="M0 7a3 3 0 0 1 6 0z" fill="#fff"/></svg>JOIN FOR FREE!</a>
  <nav class="abs nav">
    <a class="active">HOME</a><a>IDIOMS</a><a>COMMON ERRORS</a><a>CROSSWORD</a><a>BLOG</a><a>CONTACT</a>
  </nav>
  <div class="abs header-rule"></div>
</header>

<section class="abs hero">
  <div class="abs hero-photo" role="img" aria-label="Photo of a reader holding an open dictionary"></div>
</section>
<h1 class="abs hero-title">LUMO ENGLISH DICTIONARY</h1>
<div class="abs search">
  <div class="search-input">Enter a word or phase</div>
  <div class="search-btn">SEARCH</div>
</div>
<div class="abs search-hint">(eg. vexed, synonym, sonnet)</div>
<div class="abs dots"><span></span><span></span><span class="on"></span><span></span></div>

<aside>
  <div class="abs card card-word">
    <div class="card-head">WORD OF THE DAY</div>
    <div class="word-tile">VEXED</div>
    <p>Lorem ipsum dolor sit amet, consectetur adipiscing elit. Duis vel felis venenatis, placerat nulla non, hendrerit nisi.</p>
  </div>
  <div class="abs card card-tidbit">
    <div class="card-head">ENGLISH TIDBIT</div>
    <div class="word-tile">GIBE/JIBE</div>
    <p>To "gibe" is to taunt. Gibe is however slowly going out of use. Jibe means to agree but is often used in the negative sense. Although the versions of the tricksters jibed, the police officer suspected that there was something wrong.</p>
  </div>
</aside>

<section class="abs main features">
  <h2>Search, Save and Master Words</h2>
  <ul class="feature-list">
    <li><span class="bullet"></span>Search from more than 300,000 words and phrases</li>
    <li><span class="bullet"></span>Save the words to your personal deck and access from anywhere</li>
    <li><span class="bullet"></span>Multiple usages to clarify the context</li>
    <li><span class="bullet"></span>It's FREE</li>
    <li><span class="bullet"></span>Audio, phonetics, meanings, synonyms and antonyms</li>
  </ul>
  <div class="btn btn-cta">
    <svg width="7" height="8" viewBox="0 0 6 7"><circle cx="3" cy="2" r="1.7" fill="#fff"/><path d="M0 7a3 3 0 0 1 6 0z" fill="#fff"/></svg>JOIN FOR FREE!</div>
  <div class="divider" style="margin-top:17px"></div>
</section>

<section class="abs main crossword">
  <h2>Daily Crossword</h2>
  <div class="kicker">Crossword Lovers!</div>
  <p class="body-text">Lorem ipsum dolor sit amet, consectetur adipiscing elit. Duis vel felis venenatis, placerat nulla non, hendrerit nisi. Sed vitae pharetra libero, ut dapibus orci. Suspendisse feugiat libero non diam consectetur suscipit. Fusce id sem sagittis, ultrices neque non, dictum elit.</p>
  <div class="btn btn-blue">SOLVE NOW</div>
  <div class="divider" style="margin-top:22px"></div>
</section>
<div class="abs crossword-art" role="img" aria-label="Illustration of a crossword puzzle board"></div>

<section class="abs main addon">
  <h2>Orbelle Browser Addon</h2>
  <p class="body-text" style="margin-top:8px;width:310px">Add this tool to your Orbelle Browser and quickly look up for definitions from any website without leaving the page.</p>
  <div class="btn btn-blue">GET IT NOW</div>
  <div class="divider" style="margin-top:22px"></div>
</section>
<div class="abs addon-shot" role="img" aria-label="Screenshot of the browser addon definition popup"></div>

<section class="abs browse">
  <h2>Browse Dictionary</h2>
  <div class="letters">
    <span>A</span><span>B</span><span>C</span><span>D</span><span>E</span><span>F</span><span>G</span><span>H</span><span>I</span><span>J</span><span>K</span><span>L</span><span>M</span><span>N</span><span>O</span><span>P</span><span>Q</span><span>R</span><span>S</span><span>T</span><span>U</span><span>V</span><span>W</span><span>X</span><span>Y</span><span>Z</span>
  </div>
</section>

<section class="abs mobile">
  <h2>Designed for Pocketphone</h2>
  <p>Cras dictum, odio a volutpat varius, lacus velit tempus justo, eu tincidunt lorem leo at nisl. Sed fermentum diam feugiat, suscipit nisl sed, vestibulum lorem. Integer at ultrices elit. Quisque vitae ipsum lorem. Pellentesque habitant morbi tristique senectus et netus et malesuada fames ac turpis egestas. Vestibulum eget elit finibus, dictum nibh in, feugiat arcu. Donec congue, erat nec iaculis aliquam, dui libero semper libero, sit amet sagittis mi nunc sed tellus. Aenean pulvinar neque non elit rhoncus tempor.</p>
  <div class="phone-art" role="img" aria-label="Illustration of a smartphone"></div>
</section>

<footer class="abs footer">
  <div class="foot-col" style="left:64px"><h3>Lumo Wordfind</h3>
    <ul><li>Meaning/Definition,</li><li>Audio</li><li>Phonetics</li></ul></div>
  <div class="foot-col" style="left:210px"><h3>LumoWordfind.com</h3>
    <ul><li>FAQ</li><li>Contact</li><li>Blog</li></ul></div>
  <div class="foot-col" style="left:355px"><h3>Others</h3>
    <ul><li>Popular Words</li><li>Common Errors in English</li><li>Prep Online</li></ul></div>
  <div class="foot-col" style="left:501px"><h3>Legal</h3>
    <ul><li>Privacy Policy</li><li>Terms of Use</li></ul></div>
  <div class="copyright">Copyright@2016 Lumo Wordfind. All Right Reserved.</div>
  <div class="social">
    <span style="background:#3b5b9a"></span><span style="background:#3a9ad9"></span><span style="background:#d34836"></span><span style="background:#f0902c"></span>
  </div>
</footer>

</body>
</html>
```